Inspiring Fundraising Foundation Website to Provide Academic Scholarships

Hello, we are launching a foundation to provide academic scholarships to high school students for college. We'd like this to be an informational website with contact information. There will be a total of approximately 5-7 pages in all.
The color scheme will be purple and white, with a girly feel. I 've attached the logo for reference!

Target Market(s)

high school students, college students

Industry/Entity Type

Education

Coding

Coded - Design and coding required

Number of Pages Required

5+ page

Font styles to use
Serif
Sans Serif
Script

Colors
6b449b
886aae
b7a5cd
e4daeb
ffffff
fdf9cf
fbf289

Requirements
Must have
• Purple, girly feel, to reflect the logo's style. Should be light-themed
Should not have
• No dark themes (aka heavy on black or dark colors)

```html
<!DOCTYPE html>
<html lang="en">
<head>
<meta charset="utf-8">
<title>Marisol Arden Foundation</title>
<link href="https://fonts.googleapis.com/css2?family=Ubuntu:wght@400;500;700&family=Open+Sans:wght@400;600&family=Roboto:wght@400;500;700&display=swap" rel="stylesheet">
<style>
:root{
  --purple-deep:#3d1a5c;
  --purple:#6b449b;
  --purple-mid:#886aae;
  --purple-soft:#b7a5cd;
  --lilac:#e4daeb;
  --white:#ffffff;
  --cream:#fdf9cf;
  --yellow:#fbf289;
  --ink:#222222;
  --text:#444444;
  --footer:#f1f1f1;
  --bar:#d9d9d9;
}
*{margin:0;padding:0;box-sizing:border-box}
html,body{width:1200px;height:2791px;overflow:hidden}
body{position:relative;background:var(--white);font-family:"Open Sans",sans-serif;color:var(--text)}
.abs{position:absolute}

/* header */
.site-header{position:absolute;left:0;top:0;width:1200px;height:128px;background:var(--white);z-index:3}
.brand-badge{position:absolute;left:95px;top:30px;width:190px;height:190px;border-radius:50%;background:var(--white);z-index:4;display:flex;flex-direction:column;align-items:center;justify-content:center;text-align:center}
.brand-badge span{font-family:"Ubuntu",sans-serif;font-weight:500;color:var(--purple-deep);font-size:24px;line-height:1.15}
.topbar{position:absolute;right:100px;top:24px;display:flex;align-items:center;gap:12px;font-family:"Roboto",sans-serif;font-size:17px;color:var(--ink)}
.social-dot{width:32px;height:32px;border:2px solid var(--ink);border-radius:50%}
.contact-chip{display:flex;align-items:center;gap:10px;margin-left:16px}
.contact-chip .chip-icon{width:34px;height:34px;border-radius:50%;display:flex;align-items:center;justify-content:center}
.mail-chip .chip-icon{background:var(--purple-deep)}
.mail-chip a{color:var(--purple-deep);text-decoration:none}
.phone-chip .chip-icon{background:#444}
.main-nav{position:absolute;right:100px;top:88px;display:flex;gap:30px;font-family:"Roboto",sans-serif;font-size:16px;font-weight:500;color:var(--ink)}
.main-nav .current{color:var(--purple-deep)}

/* hero */
.hero{position:absolute;left:0;top:128px;width:1200px;height:540px;overflow:hidden}
.hero-photo{position:absolute;inset:0;background:linear-gradient(120deg,#8a7a70 0%,#b9a998 30%,#6d5d58 55%,#a89285 80%,#5d4a4a 100%)}
.hero-shade{position:absolute;inset:0;background:linear-gradient(90deg,rgba(0,0,0,0) 40%,rgba(30,10,40,.35) 100%)}
.hero-title{position:absolute;right:100px;top:130px;font-family:"Ubuntu",sans-serif;font-weight:700;font-size:52px;color:var(--white);letter-spacing:1px}
.hero-text{position:absolute;right:100px;top:210px;width:520px;text-align:right;font-family:"Ubuntu",sans-serif;font-size:15px;line-height:26px;color:var(--white)}
.hero-btn{position:absolute;right:100px;top:287px;width:140px;height:56px;border:2px solid var(--white);color:var(--white);font-family:"Ubuntu",sans-serif;font-size:16px;display:flex;align-items:center;justify-content:center}
.hero-dots{position:absolute;right:100px;top:378px;display:flex;gap:6px}
.hero-dots i{width:14px;height:14px;border:2px solid var(--white);border-radius:50%}
.hero-dots i.on{background:var(--purple-deep)}
.hero-wave{position:absolute;left:0;bottom:0;width:1200px;height:130px}

/* about */
.section-title{font-family:"Ubuntu",sans-serif;font-weight:500;font-size:28px;color:var(--purple-deep)}
.title-rule{height:2px;width:208px;background:var(--purple-deep);margin-top:10px}
.about{position:absolute;left:100px;top:738px;width:540px}
.about p{font-size:13.5px;line-height:25px;color:var(--text);margin-top:12px}
.about .title-rule{width:210px;margin-bottom:10px}
.btn-solid{display:inline-flex;align-items:center;justify-content:center;background:var(--purple-deep);color:var(--white);font-family:"Roboto",sans-serif;font-weight:500;font-size:15px;width:112px;height:42px;margin-top:18px}
.video-frame{position:absolute;left:697px;top:744px;width:400px;height:283px;box-shadow:0 18px 26px rgba(0,0,0,.25)}
.video-still{position:absolute;inset:0;background:linear-gradient(135deg,#d8c7a8 0%,#c9a57e 35%,#6f8fb5 60%,#e2d6c0 100%)}
.video-controls{position:absolute;left:10px;right:10px;bottom:8px;height:22px;background:rgba(30,30,40,.75)}
.video-play{position:absolute;left:168px;top:110px}

/* scholarships */
.scholarships{position:absolute;left:0;top:1107px;width:1200px;height:491px;background:var(--yellow)}
.scholarships .section-title{position:absolute;left:0;width:1200px;top:48px;text-align:center}
.scholarships .title-rule{position:absolute;left:554px;top:99px;width:92px;margin:0}
.program{position:absolute;top:156px;width:200px;text-align:center}
.program svg{display:block;margin:0 auto}
.program h3{font-family:"Roboto",sans-serif;font-weight:500;font-size:17px;color:var(--ink);margin-top:18px}
.program p{font-family:"Roboto",sans-serif;font-size:12.5px;line-height:20px;color:#333;margin-top:12px}

/* story */
.story-photo{position:absolute;left:99px;top:1659px;width:316px;height:316px;border-radius:50%;border:3px solid var(--purple-deep);padding:8px;background:var(--white)}
.story-photo div{width:100%;height:100%;border-radius:50%;background:linear-gradient(180deg,#f2f0ee 0%,#e6e2df 55%,#c0584f 75%,#a0413c 100%)}
.story{position:absolute;left:460px;top:1684px;width:640px}
.story .title-rule{width:112px;margin-bottom:8px}
.story p{font-size:13.5px;line-height:26px;color:var(--text);margin-top:12px}

/* newsletter */
.newsletter{position:absolute;left:0;top:2024px;width:1200px;height:400px;background:linear-gradient(100deg,#4a1f6e 0%,#5b2c80 50%,#4a1f6e 100%);overflow:hidden}
.newsletter-cap{position:absolute;left:120px;top:88px}
.newsletter h2{position:absolute;left:374px;top:60px;font-family:"Ubuntu",sans-serif;font-weight:500;font-size:27px;color:var(--white)}
.newsletter p{position:absolute;left:374px;top:110px;width:730px;font-size:13.5px;line-height:24px;color:var(--white)}
.email-field{position:absolute;left:376px;top:186px;width:375px;height:46px;border-radius:6px;background:rgba(255,255,255,.75);font-family:"Roboto",sans-serif;font-size:16px;color:#555;padding:13px 16px}
.subscribe-btn{position:absolute;left:771px;top:186px;width:170px;height:46px;border:2px solid var(--white);color:var(--white);font-family:"Roboto",sans-serif;font-weight:500;font-size:15px;display:flex;align-items:center;justify-content:center}
.newsletter-wave{position:absolute;left:0;bottom:0;width:1200px;height:170px}

/* footer */
.site-footer{position:absolute;left:0;top:2424px;width:1200px;height:305px;background:var(--footer)}
.footer-brand{position:absolute;left:100px;top:96px;width:150px;text-align:center;font-family:"Ubuntu",sans-serif;font-weight:500;font-size:26px;line-height:1.15;color:var(--purple-deep)}
.footer-col{position:absolute;top:18px}
.footer-col h4{font-family:"Roboto",sans-serif;font-weight:700;font-size:16px;color:var(--purple-deep)}
.footer-col .title-rule{width:74px;height:2px;margin:10px 0 14px}
.quick-links{left:333px}
.quick-links li{list-style:none;font-family:"Roboto",sans-serif;font-size:14px;color:#333;line-height:32px}
.contact-col{left:512px;width:270px}
.contact-row{display:flex;gap:14px;margin-bottom:14px}
.contact-row .ring{flex:none;width:36px;height:36px;border:2px solid var(--purple-deep);border-radius:50%;display:flex;align-items:center;justify-content:center}
.contact-row b{display:block;font-family:"Roboto",sans-serif;font-size:13px;font-weight:700;color:var(--ink)}
.contact-row span{font-family:"Roboto",sans-serif;font-size:12px;line-height:20px;color:#333}
.form-col{left:813px}
.form-col .title-rule{width:132px}
.field{position:absolute;border:1px solid #999;background:var(--white);font-family:"Roboto",sans-serif;font-size:11px;color:#444;padding:8px 10px}
.send-btn{position:absolute;left:0;top:198px;width:118px;height:36px;background:var(--purple-deep);color:var(--white);font-family:"Roboto",sans-serif;font-weight:500;font-size:12px;display:flex;align-items:center;justify-content:center}

.bottom-bar{position:absolute;left:0;top:2729px;width:1200px;height:62px;background:var(--bar)}
.bottom-bar p{position:absolute;left:100px;top:22px;font-family:"Roboto",sans-serif;font-size:14px;color:#333}
.bottom-social{position:absolute;left:874px;top:14px;display:flex;gap:9px}
.bottom-social i{width:34px;height:34px;border:2px solid #333;border-radius:50%}
</style>
</head>
<body>

<header class="site-header">
  <div class="topbar">
    <i class="social-dot"></i><i class="social-dot"></i><i class="social-dot"></i><i class="social-dot"></i>
    <span class="contact-chip mail-chip">
      <span class="chip-icon"><svg width="16" height="12" viewBox="0 0 16 12"><rect x="1" y="1" width="14" height="10" fill="none" stroke="#fff" stroke-width="1.6"/><path d="M1 1l7 6 7-6" fill="none" stroke="#fff" stroke-width="1.6"/></svg></span>
      <a>info@marisolarden.org</a>
    </span>
    <span class="contact-chip phone-chip">
      <span class="chip-icon"><svg width="14" height="16" viewBox="0 0 14 16"><path d="M3 1l3 3-2 2c1 2 3 4 5 5l2-2 3 3-2 3C6 14 0 8 1 3z" fill="#fff"/></svg></span>
      <span>180 555 0147</span>
    </span>
  </div>
  <nav class="main-nav">
    <span class="current">HOME</span><span>COURSES</span><span>FEATURES</span><span>EVENTS</span><span>SCHOLARSHIPS</span><span>BLOG</span><span>CONTACT</span>
  </nav>
</header>
<div class="brand-badge"><span>Marisol<br>Arden<br>Foundation</span></div>

<section class="hero">
  <div class="hero-photo" role="img" aria-label="Young children smiling at their desks in a bright classroom"></div>
  <div class="hero-shade"></div>
  <h1 class="hero-title">MARISOL ARDEN</h1>
  <p class="hero-text">Duis aute irure dolor in reprehenderit in voluptate velit esse cillum dolore eu fugiat nulla pariatur.</p>
  <span class="hero-btn">Read More</span>
  <div class="hero-dots"><i class="on"></i><i></i><i></i><i></i><i></i></div>
  <svg class="hero-wave" viewBox="0 0 1200 130" preserveAspectRatio="none">
    <path d="M0 95 C300 40 500 130 800 90 C1000 62 1120 40 1200 20 L1200 130 L0 130Z" fill="#fbf289"/>
    <path d="M0 110 C300 55 500 140 800 100 C1000 78 1120 58 1200 42 L1200 130 L0 130Z" fill="#ffffff"/>
  </svg>
</section>

<section class="about">
  <h2 class="section-title">About Marisol Arden Foundation</h2>
  <div class="title-rule"></div>
  <p>The Marisol Arden Foundation is dedicated to helping Houston young men and women reach their goal of starting a real estate career. Our foundation will work to make a difference by offering scholarships and internships for future agents.</p>
  <p>The foundation will award scholarships to two hard working juniors or seniors in college per year. To be eligible, applicants must send their resume and a 1-2 page essay stating why they are passionate in real estate and what they hope to achieve. Application will open February 20th, 2017 and close May 1st, 2017.</p>
  <span class="btn-solid">Read More</span>
</section>
<div class="video-frame">
  <div class="video-still" role="img" aria-label="Video still of students writing together at a classroom table"></div>
  <svg class="video-play" width="56" height="56" viewBox="0 0 56 56"><circle cx="28" cy="28" r="25" fill="rgba(0,0,0,.35)" stroke="#fff" stroke-width="3"/><path d="M22 17l17 11-17 11z" fill="#fff"/></svg>
  <div class="video-controls"></div>
</div>

<section class="scholarships">
  <h2 class="section-title">Our Scholarships</h2>
  <div class="title-rule"></div>

  <div class="program" style="left:90px">
    <svg width="170" height="180" viewBox="0 0 170 180"><path d="M85 6a79 79 0 0 1 22 155l-22 17-22-17A79 79 0 0 1 85 6z" fill="none" stroke="#3d1a5c" stroke-width="3"/>
      <g fill="#3d1a5c"><circle cx="85" cy="70" r="11"/><path d="M66 103a19 19 0 0 1 38 0z"/><circle cx="58" cy="76" r="9"/><path d="M42 103a16 16 0 0 1 28-10v10z"/><circle cx="112" cy="76" r="9"/><path d="M128 103a16 16 0 0 0-28-10v10z"/></g></svg>
    <h3>School Students</h3><p>Our team at Bright Path may be small, but it's the exact size we need to make sure.</p>
  </div>
  <div class="program" style="left:298px">
    <svg width="170" height="180" viewBox="0 0 170 180"><path d="M85 6a79 79 0 0 1 22 155l-22 17-22-17A79 79 0 0 1 85 6z" fill="#3d1a5c" stroke="#3d1a5c" stroke-width="3"/>
      <g fill="#fff"><circle cx="85" cy="60" r="14"/><rect x="74" y="56" width="22" height="5" fill="#3d1a5c"/><path d="M60 118c0-22 10-34 25-34s25 12 25 34z"/><path d="M85 84l-4 8 4 20 4-20z" fill="#3d1a5c"/><path d="M104 96l20-22" stroke="#fff" stroke-width="3"/></g></svg>
    <h3>Fundraising Foundation</h3><p>Our team at Bright Path may be small, but it's the exact size we need to make sure.</p>
  </div>
  <div class="program" style="left:506px">
    <svg width="170" height="180" viewBox="0 0 170 180"><path d="M85 6a79 79 0 0 1 22 155l-22 17-22-17A79 79 0 0 1 85 6z" fill="none" stroke="#3d1a5c" stroke-width="3"/>
      <g fill="#3d1a5c"><rect x="84" y="52" width="44" height="32" fill="none" stroke="#3d1a5c" stroke-width="4"/><circle cx="64" cy="64" r="9"/><path d="M48 106c0-16 7-26 16-26 7 0 12 4 22-2l3 6c-8 6-13 7-17 7v15z"/><path d="M92 76l10-10 8 6 10-12" fill="none" stroke="#3d1a5c" stroke-width="3"/><circle cx="64" cy="112" r="9"/><circle cx="92" cy="112" r="9"/></g></svg>
    <h3>Academic Scholarships</h3><p>Our team at Bright Path may be small, but it's the exact size we need to make sure.</p>
  </div>
  <div class="program" style="left:718px">
    <svg width="170" height="180" viewBox="0 0 170 180"><path d="M85 6a79 79 0 0 1 22 155l-22 17-22-17A79 79 0 0 1 85 6z" fill="none" stroke="#3d1a5c" stroke-width="3"/>
      <g fill="#3d1a5c"><rect x="52" y="56" width="66" height="46" rx="3" fill="none" stroke="#3d1a5c" stroke-width="5"/><rect x="78" y="102" width="14" height="10"/><rect x="68" y="112" width="34" height="5"/><path d="M76 92l30-30 6 6-30 30-9 3z"/></g></svg>
    <h3>School Services</h3><p>Our team at Bright Path may be small, but it's the exact size we need to make sure.</p>
  </div>
  <div class="program" style="left:919px">
    <svg width="170" height="180" viewBox="0 0 170 180"><path d="M85 6a79 79 0 0 1 22 155l-22 17-22-17A79 79 0 0 1 85 6z" fill="none" stroke="#3d1a5c" stroke-width="3"/>
      <g fill="#3d1a5c"><path d="M85 42l28 11-28 11-28-11z"/><path d="M71 58v10c8 6 20 6 28 0V58"/><circle cx="85" cy="76" r="10"/><path d="M56 92l29 8 29-8v28l-29 8-29-8z"/><path d="M85 100v28" stroke="#fff" stroke-width="2"/></g></svg>
    <h3>Expert Consulting</h3><p>Our team at Bright Path may be small, but it's the exact size we need to make sure.</p>
  </div>
</section>

<div class="story-photo"><div role="img" aria-label="Portrait of the foundation's namesake seated on a red armchair"></div></div>
<section class="story">
  <h2 class="section-title">Our Story</h2>
  <div class="title-rule"></div>
  <p>Marisol Arden was a significant contributor to the beginning of Bellwood and Company Properties. As one of the company's first employees, her plan was to work as an Administrative Assistant while she finished her undergraduate degree in Business Administration at Gulf Coast University. With plans to graduate in December of 2016, she couldn't wait to begin her real estate career, since she had just obtained her Real Estate license in 2014.</p>
  <p>However, on January 23rd, 2015, she was heading home from the Grand Opening party for Bellwood and Co. Properties when she was struck by a drunk driver and killed at the scene.</p>
</section>

<section class="newsletter">
  <svg class="newsletter-cap" width="180" height="120" viewBox="0 0 180 120"><path d="M90 6l86 34-86 34L4 40z" fill="#fff"/><path d="M46 60v30c24 18 64 18 88 0V60L90 78z" fill="#fff"/><path d="M160 46v46" stroke="#fff" stroke-width="4"/><rect x="154" y="90" width="12" height="22" rx="3" fill="#fff"/></svg>
  <h2>Academic scholarships to high school students</h2>
  <p>The Marisol Arden foundation will work to make a difference by not only offering scholarships and internships for future agents but by taking a stand against drinking and driving, an issue.</p>
  <div class="email-field">Email Address</div>
  <span class="subscribe-btn">SUBSCRIBE NOW</span>
  <svg class="newsletter-wave" viewBox="0 0 1200 170" preserveAspectRatio="none">
    <path d="M0 150 C250 40 500 70 750 110 C950 140 1100 120 1200 60 L1200 170 L0 170Z" fill="#fbf289"/>
    <path d="M0 168 C250 65 500 95 750 132 C950 160 1100 145 1200 88 L1200 170 L0 170Z" fill="#f1f1f1"/>
  </svg>
</section>

<footer class="site-footer">
  <div class="footer-brand">Marisol<br>Arden<br>Foundation</div>
  <div class="footer-col quick-links">
    <h4>QUICK LINKS</h4><div class="title-rule"></div>
    <ul><li>› Home</li><li>› Courses</li><li>› Features</li><li>› Events</li><li>› Scholarships</li><li>› Contact Us</li></ul>
  </div>
  <div class="footer-col contact-col">
    <h4>CONTACT US</h4><div class="title-rule"></div>
    <div class="contact-row"><span class="ring"><svg width="12" height="16" viewBox="0 0 12 16"><path d="M6 1a5 5 0 0 1 5 5c0 4-5 9-5 9S1 10 1 6a5 5 0 0 1 5-5z" fill="#3d1a5c"/><circle cx="6" cy="6" r="2" fill="#fff"/></svg></span><div><b>MARISOL ARDEN FOUNDATION,</b><span>48 Willow Lane, Suite 200<br>Scottsdale, AZ 85250</span></div></div>
    <div class="contact-row"><span class="ring"><svg width="10" height="16" viewBox="0 0 10 16"><rect x="1" y="1" width="8" height="14" rx="1.5" fill="none" stroke="#3d1a5c" stroke-width="1.8"/><circle cx="5" cy="12.5" r="1" fill="#3d1a5c"/></svg></span><div><b>PHONE:</b><span>180 555 0147</span></div></div>
    <div class="contact-row"><span class="ring"><svg width="16" height="16" viewBox="0 0 16 16"><circle cx="8" cy="8" r="7" fill="#3d1a5c"/><rect x="4" y="5" width="8" height="6" fill="#fff"/><path d="M4 5l4 3 4-3" fill="none" stroke="#3d1a5c" stroke-width="1"/></svg></span><div><b>Mail:</b><span>info@marisolarden.org</span></div></div>
  </div>
  <div class="footer-col form-col" style="width:287px;height:240px">
    <h4>CONTACT FORM</h4><div class="title-rule"></div>
    <div class="field" style="left:0;top:72px;width:137px;height:34px">Name</div>
    <div class="field" style="left:149px;top:72px;width:138px;height:34px">Phone</div>
    <div class="field" style="left:0;top:117px;width:287px;height:62px">Message</div>
    <span class="send-btn">SEND MESSAGE</span>
  </div>
</footer>

<div class="bottom-bar">
  <p>Copyright © 2017 Marisol Arden Foundation. All Rights Reserved.</p>
  <div class="bottom-social"><i></i><i></i><i></i><i></i><i></i></div>
</div>

</body>
</html>
```